Investment company needing business card

We are wanting a business card which looks sharp and easy on the eye. We are thinking of having a business card with the logo embossed on it, to really make it stand out. We will only have a small amount of information of the business card, person's name, position, email address and phone number

Contact Information for Business Card

Danielle Frost
Executive Assistant
+64 21 473 5162
danielf@harwickpartners.co.nz

Requirements
Must have
• Embossed logo
Should not have
• Not to be busy

```html
<!DOCTYPE html>
<html lang="en">
<head>
<meta charset="utf-8">
<title>Harwick Partners – Business Card</title>
<link href="https://fonts.googleapis.com/css2?family=Lato:wght@400;700;900&display=swap" rel="stylesheet">
<style>
  :root {
    --backdrop: #666666;
    --card-white: #ffffff;
    --brand-green: #25b574;
    --ink: #3a3a3a;
    --brand-grey: #5e5e5e;
    --rule: #b5b5b5;
  }
  html, body {
    margin: 0;
    padding: 0;
    width: 1200px;
    height: 802px;
    overflow: hidden;
    background: var(--backdrop);
    font-family: "Lato", sans-serif;
  }
  .canvas {
    position: relative;
    width: 1200px;
    height: 802px;
  }
  .card {
    position: absolute;
    top: 274px;
    width: 443px;
    height: 265px;
  }
  .card--front {
    left: 136px;
    background: var(--card-white);
  }
  .card--back {
    left: 624px;
    background: var(--brand-green);
  }
  .brand {
    position: absolute;
    right: 26px;
    top: 66px;
    display: flex;
    align-items: center;
    gap: 8px;
  }
  .brand__square {
    width: 30px;
    height: 30px;
    background: var(--brand-grey);
  }
  .brand__name {
    font-weight: 900;
    font-size: 19px;
    letter-spacing: 0.5px;
    color: var(--brand-green);
    line-height: 1;
  }
  .person__name {
    position: absolute;
    left: 28px;
    top: 156px;
    margin: 0;
    font-weight: 700;
    font-size: 18px;
    letter-spacing: 0.3px;
    color: var(--brand-green);
    line-height: 1;
  }
  .person__title {
    position: absolute;
    left: 28px;
    top: 179px;
    margin: 0;
    font-size: 12.5px;
    color: var(--ink);
    line-height: 1;
  }
  .person__rule {
    position: absolute;
    left: 144px;
    width: 273px;
    top: 185px;
    height: 1px;
    background: var(--rule);
  }
  .contact {
    position: absolute;
    right: 26px;
    top: 206px;
    margin: 0;
    padding: 0;
    list-style: none;
    text-align: right;
    font-size: 12.5px;
    color: var(--ink);
  }
  .contact__item {
    display: flex;
    justify-content: flex-end;
    align-items: center;
    gap: 3px;
    height: 16px;
  }
  .contact__icon {
    width: 9px;
    height: 9px;
    fill: var(--brand-green);
  }
  .back-brand {
    position: absolute;
    inset: 0;
    display: flex;
    align-items: center;
    justify-content: center;
    font-weight: 900;
    font-size: 30px;
    letter-spacing: 1px;
    color: var(--card-white);
  }
</style>
</head>
<body>
<main class="canvas">
  <section class="card card--front" aria-label="Business card front">
    <div class="brand">
      <span class="brand__square"></span>
      <span class="brand__name">HARWICK PARTNERS</span>
    </div>
    <h1 class="person__name">DANIELLE FROST</h1>
    <p class="person__title">Executive Assistant</p>
    <span class="person__rule"></span>
    <ul class="contact">
      <li class="contact__item">+64 21 473 5162
        <svg class="contact__icon" viewBox="0 0 10 10" aria-hidden="true"><path d="M1 3.2C1 2 2.5 1 5 1s4 1 4 2.2L7.6 3.8 6.8 3H3.2l-.8.8zM2.5 4.5h5L9 9H1z"/></svg>
      </li>
      <li class="contact__item">danielf@harwickpartners.co.nz
        <svg class="contact__icon" viewBox="0 0 10 10" aria-hidden="true"><path d="M0 1.5h10v7H0z M0.8 2.2L5 5.5 9.2 2.2" stroke="#fff" stroke-width="0.8"/></svg>
      </li>
    </ul>
  </section>
  <section class="card card--back" aria-label="Business card back">
    <div class="back-brand">HARWICK PARTNERS</div>
  </section>
</main>
</body>
</html>
```